we can communicate on this, but i want to follow the approach we took on Pellew|Marsh & Quinlan but i feel the card front needs the black background and the platinum and gold logo. The back? I am open. we can use the same info from PM&Q. Velmont Arc is an enhanced equity investment fund - basically a very exclusive boutique hedge fund that uses only stock options. very advanced things. hope you are interested

Contact Information for Business Card

Dr. Lewis T. Brennick, CFA
Scientifique de fusée financière
701.555.0143
LTBquant47@mailvantor.com

4718 Willow Creek Bend W.
West Fargo, ND 58078

No web site

Colors

Designer to choose colors to be used in the design.

Requirements
Nice to have
• I tend to prefer the most visible applications of the logo to include logo and name, the logo version with a black background and the gold and platinum components separated by the black. I see this working well for a single side (logo and name - this is card front to me).
• I am fairly open to other treatments on the reverse side with the data. To me, it makes sense to have a different color rendition of the logo on the reverse and it may be a muted black tone on tone or an oversized portion that would have spot UV. Or, the reverse may play with colors and layout
Should not have
• Other colors = no no
• Decorative font

```html
<!DOCTYPE html>
<html lang="en">
<head>
<meta charset="UTF-8">
<title>Velmont Arc — Business Card</title>
<link rel="stylesheet" href="https://fonts.googleapis.com/css2?family=Montserrat:wght@400;500;700&display=swap">
<style>
  :root {
    --backdrop: #2b2b2b;
    --card-black: #141414;
    --gold: #f2b51c;
    --platinum: #e6e6e6;
    --muted: #bdbdbd;
  }
  * { box-sizing: border-box; margin: 0; padding: 0; }
  html, body { width: 800px; height: 1200px; overflow: hidden; }
  body {
    background: var(--backdrop);
    font-family: "Montserrat", Arial, sans-serif;
    position: relative;
  }
  .card {
    position: absolute;
    left: 80px;
    width: 640px;
    height: 366px;
    background: var(--card-black);
    border-radius: 4px;
    box-shadow: 0 18px 40px rgba(0,0,0,0.45);
    overflow: hidden;
  }
  .card--front { top: 150px; }
  .card--back { top: 684px; }

  /* Front: gold and platinum brand on black */
  .front-brand {
    position: absolute;
    inset: 0;
    display: flex;
    flex-direction: column;
    align-items: center;
    justify-content: center;
    gap: 20px;
  }
  .front-brand__dot {
    width: 112px; height: 112px;
    border-radius: 50%;
    background: var(--gold);
  }
  .front-brand__name {
    font-weight: 700;
    font-size: 48px;
    letter-spacing: 1px;
    color: var(--platinum);
    white-space: nowrap;
  }

  /* Back: contact details */
  .contact {
    position: absolute;
    left: 42px;
    top: 104px;
  }
  .contact__name {
    font-weight: 500;
    font-size: 20px;
    color: var(--gold);
  }
  .contact__title {
    font-size: 12px;
    color: var(--muted);
    margin-top: 3px;
    margin-bottom: 22px;
  }
  .contact__row {
    display: flex;
    align-items: flex-start;
    gap: 12px;
    font-size: 13px;
    line-height: 1.45;
    color: var(--platinum);
    margin-bottom: 7px;
  }
  .contact__icon { width: 14px; height: 14px; flex: none; margin-top: 3px; }

  .back-brand {
    position: absolute;
    right: 58px;
    top: 118px;
    display: flex;
    flex-direction: column;
    align-items: center;
    gap: 14px;
  }
  .back-brand__dot {
    width: 76px; height: 76px;
    border-radius: 50%;
    background: var(--gold);
  }
  .back-brand__name {
    font-weight: 700;
    font-size: 30px;
    letter-spacing: 1px;
    color: var(--platinum);
    white-space: nowrap;
  }
</style>
</head>
<body>
  <section class="card card--front" aria-label="Card front">
    <div class="front-brand">
      <div class="front-brand__dot"></div>
      <div class="front-brand__name">VELMONT ARC</div>
    </div>
  </section>

  <section class="card card--back" aria-label="Card back">
    <div class="contact">
      <div class="contact__name">Reid Halvor Lantz</div>
      <div class="contact__title">Managing Director</div>

      <div class="contact__row">
        <svg class="contact__icon" viewBox="0 0 14 14"><path d="M3 1h2.5l1 3-1.6 1.2a7 7 0 0 0 3.9 3.9L10 7.5l3 1V11a2 2 0 0 1-2 2A10 10 0 0 1 1 3a2 2 0 0 1 2-2z" fill="var(--gold)"/></svg>
        <span>609 555-0187</span>
      </div>
      <div class="contact__row">
        <svg class="contact__icon" viewBox="0 0 14 14"><rect x="1" y="3" width="12" height="8.5" rx="1" fill="var(--gold)"/><path d="M1.5 3.5 7 8l5.5-4.5" stroke="var(--card-black)" stroke-width="1.2" fill="none"/></svg>
        <span>info@corvalisite.com</span>
      </div>
      <div class="contact__row">
        <svg class="contact__icon" viewBox="0 0 14 14"><path d="M7 13S2.5 8.2 2.5 5a4.5 4.5 0 0 1 9 0C11.5 8.2 7 13 7 13z" fill="var(--gold)"/><circle cx="7" cy="5" r="1.6" fill="var(--card-black)"/></svg>
        <span>812 Larkspur St., Dunmore City,<br>Elk Valley, US 104257</span>
      </div>
    </div>

    <div class="back-brand">
      <div class="back-brand__dot"></div>
      <div class="back-brand__name">VELMONT ARC</div>
    </div>
  </section>
</body>
</html>
```